Chimney Service company needs new business card design

We need a updated business card with our new logo added. We provide a full range of chimney services throughout Vermont and New Hampshire. The business card will be one sided and color. Attached is our current business card another document showing all the information we would like on the card.
We dont like a lot of flashy colors.... here is a link to our website to get an idea of our branding www.flueguardianvt.example

Target Market(s)

homeowners

Industry/Entity Type

Business

Contact Information for Business Card

See attached sheet for content.

Font styles to use
Serif
Sans Serif

Requirements
Must have
• all information provided on separate sheet
Should not have
• Additional information that may clogg up design

```html
<!DOCTYPE html>
<html lang="en">
<head>
<meta charset="utf-8">
<title>Flue Guardian – Business Card</title>
<link rel="stylesheet" href="https://fonts.googleapis.com/css2?family=Cinzel:wght@500&family=Oswald:wght@500&family=Roboto:wght@400&display=swap">
<style>
  :root {
    --backdrop: #2b2b2b;
    --card-white: #f3f3f1;
    --brand-red: #9a0a0c;
    --charcoal: #333333;
    --ink-white: #ffffff;
  }
  * { margin: 0; padding: 0; box-sizing: border-box; }
  html, body {
    width: 1200px; height: 871px; overflow: hidden;
    background: var(--backdrop);
  }
  .card {
    position: absolute; left: 100px; top: 150px;
    width: 1000px; height: 571px;
    background: var(--card-white);
    overflow: hidden;
  }
  .card-divider { position: absolute; inset: 0; width: 100%; height: 100%; }
  .brand {
    position: absolute; left: 0; top: 0; width: 460px; height: 571px;
    display: flex; flex-direction: column; align-items: center; justify-content: center;
    gap: 26px; padding-bottom: 40px;
  }
  .brand-square { width: 64px; height: 64px; background: var(--charcoal); }
  .brand-name {
    font-family: "Cinzel", serif; font-weight: 500;
    font-size: 38px; letter-spacing: 1px; color: var(--charcoal);
  }
  .details {
    position: absolute; right: 44px; top: 0; text-align: right; color: var(--ink-white);
  }
  .taglines {
    position: absolute; right: 0; top: 68px; white-space: nowrap;
    font-family: "Oswald", sans-serif; font-weight: 500; font-size: 23px;
    line-height: 32px; text-transform: uppercase;
  }
  .rule { position: absolute; right: 0; width: 42px; height: 2px; background: var(--ink-white); }
  .rule-top { top: 190px; }
  .rule-bottom { top: 391px; }
  .services, .contacts {
    position: absolute; right: 0; list-style: none; white-space: nowrap;
    font-family: "Roboto", sans-serif; font-size: 24px; line-height: 30px;
  }
  .services { top: 216px; }
  .services li::after {
    content: ""; display: inline-block; width: 8px; height: 8px; border-radius: 50%;
    background: var(--ink-white); margin-left: 12px; vertical-align: middle;
  }
  .contacts { top: 416px; line-height: 32px; }
  .contacts li { display: flex; align-items: center; justify-content: flex-end; gap: 12px; }
  .contact-icon { width: 20px; height: 20px; fill: var(--ink-white); }
</style>
</head>
<body>
  <div class="card">
    <svg class="card-divider" viewBox="0 0 1000 571" aria-hidden="true">
      <path fill="#9a0a0c" d="M520,0 Q430,290 560,571 L1000,571 L1000,0 Z"/>
      <path fill="none" stroke="#333333" stroke-width="6" d="M496,0 Q406,290 536,571"/>
    </svg>

    <div class="brand">
      <div class="brand-square"></div>
      <div class="brand-name">FLUE GUARDIAN</div>
    </div>

    <div class="details">
      <div class="taglines">
        Serving Ridgeline County since 1996<br>
        Fully insured — Free estimates<br>
        Family owned &amp; operated
      </div>
      <div class="rule rule-top"></div>
      <ul class="services">
        <li>Full Masonry Services</li>
        <li>Historic chimney restoration</li>
        <li>Stainless steel liners</li>
        <li>New Chimney installations</li>
        <li>Fully Certified Chimney sweeps</li>
      </ul>
      <div class="rule rule-bottom"></div>
      <ul class="contacts">
        <li>802-555-0143
          <svg class="contact-icon" viewBox="0 0 24 24" aria-hidden="true"><path d="M6.6 10.8c1.4 2.8 3.8 5.1 6.6 6.6l2.2-2.2c.3-.3.7-.4 1-.2 1.1.4 2.3.6 3.6.6.6 0 1 .4 1 1V20c0 .6-.4 1-1 1C10.6 21 3 13.4 3 4c0-.6.4-1 1-1h3.5c.6 0 1 .4 1 1 0 1.3.2 2.5.6 3.6.1.3 0 .7-.2 1z"/></svg>
        </li>
        <li>info@flueguardianvt.example
          <svg class="contact-icon" viewBox="0 0 24 24" aria-hidden="true"><path d="M2 5h20v14H2z"/><path d="M3 6l9 7 9-7" fill="none" stroke="#9a0a0c" stroke-width="1.6"/></svg>
        </li>
        <li>www.flueguardianvt.example
          <svg class="contact-icon" viewBox="0 0 24 24" aria-hidden="true"><circle cx="12" cy="12" r="10"/><path d="M2 12h20M12 2c3 3 3 17 0 20M12 2c-3 3-3 17 0 20" fill="none" stroke="#9a0a0c" stroke-width="1.4"/></svg>
        </li>
      </ul>
    </div>
  </div>
</body>
</html>
```